Business Card Design Project

Looking to update our business cards. We have a logo with our slogan. We are an IT firm so we wouldlike a modern look.

Industry/Entity Type

Business

```html
<!DOCTYPE html>
<html lang="en">
<head>
<meta charset="utf-8">
<title>Kernwise Inc — Business Cards</title>
<link rel="stylesheet" href="https://fonts.googleapis.com/css2?family=Fira+Sans:wght@400;500;600&display=swap">
<style>
  :root {
    --bg: #ece9e4;
    --brand-green: #6b8e2f;
    --deep-green: #2f3f1a;
    --card-white: #f7f7f5;
    --ink: #2b2b2b;
    --white: #ffffff;
  }
  * { margin: 0; padding: 0; box-sizing: border-box; }
  html, body {
    width: 1200px; height: 900px; overflow: hidden;
    background: var(--bg);
    font-family: "Fira Sans", sans-serif;
  }
  .canvas { position: relative; width: 1200px; height: 900px; }
  .card {
    position: absolute; left: 290px; width: 620px; height: 354px;
    box-shadow: 0 6px 18px rgba(0,0,0,.18);
  }
  .card--front { top: 60px; background: var(--brand-green); }
  .card--back { top: 476px; background: var(--card-white); }

  .wordmark {
    font-weight: 600; letter-spacing: 4px; text-transform: uppercase;
    white-space: nowrap;
  }
  .slogan { text-transform: uppercase; white-space: nowrap; }

  .front-brand {
    position: absolute; left: 0; right: 0; top: 120px;
    text-align: center;
  }
  .front-brand .wordmark { font-size: 54px; color: var(--white); }
  .front-brand .slogan {
    margin-top: 10px; font-size: 17px; letter-spacing: 4px;
    color: var(--deep-green);
  }

  .back-brand { position: absolute; left: 40px; top: 36px; }
  .back-brand .wordmark { font-size: 34px; color: var(--brand-green); }
  .back-brand .slogan {
    margin-top: 4px; font-size: 11px; letter-spacing: 2.6px;
    color: var(--brand-green);
  }

  .person { position: absolute; left: 46px; top: 186px; }
  .person__name { font-size: 22px; color: var(--brand-green); font-weight: 500; letter-spacing: .5px; }
  .person__title { font-size: 15px; color: var(--ink); margin-top: 2px; }

  .website {
    position: absolute; left: 46px; top: 300px;
    font-size: 16px; color: var(--brand-green);
  }
  .contact {
    position: absolute; left: 350px; top: 222px;
    font-size: 16px; color: var(--ink); line-height: 1.4;
  }
  .address {
    position: absolute; left: 340px; top: 282px;
    font-size: 17px; color: var(--ink); line-height: 1.3;
    font-style: normal;
  }
</style>
</head>
<body>
<main class="canvas">
  <section class="card card--front" aria-label="Card front">
    <div class="front-brand">
      <p class="wordmark">Kernwise</p>
      <p class="slogan">Making Technology Clear</p>
    </div>
  </section>

  <section class="card card--back" aria-label="Card back">
    <div class="back-brand">
      <p class="wordmark">Kernwise</p>
      <p class="slogan">Making Technology Clear</p>
    </div>
    <div class="person">
      <p class="person__name">MARA ELLISON</p>
      <p class="person__title">Managing Partner</p>
    </div>
    <p class="website">www.kernwiseinc.com</p>
    <div class="contact">
      <p>T: (480) 555-0148</p>
      <p>E: hello@kernwiseinc.com</p>
    </div>
    <address class="address">
      2140 W. Carver Ave Suite<br>40512 Chicago IL 60612-1180
    </address>
  </section>
</main>
</body>
</html>
```